Stylish Business Cards Wanted

- DOUBLE SIDED Design Required -

High end, edgy cards for a corporate and personal stylist. Must include logo,
Name: Belinda Harwick
Title: Director and Stylist
telephone : +61 8 7142 5809
email: belinda@theloombriefing.example
website: theloombriefing.example
Tag: Corporate Workwear & Uniform Specialist | Personal Stylist
Would like nice icons for telephone, email, website

Target Market(s)

Businesses wanting stylish uniforms, people wanting stylish wardrobes

Industry/Entity Type

Corporate Workwear Stylist

Contact Information for Business Card

I would like black, white and gold foiling incorporated in the design - possibly a touch of the other colours on my branding guide attached Name: Belinda Harwick Title: Director and Stylist telephone : +61 8 7142 5809 email: belinda@theloombriefing.example website: theloombriefing.example Tag: Corporate Workwear & Uniform Specialist | Personal Stylist Would like nice icons for telephone, email, website

Font styles to use
Other font styles liked:
• Raleway

Colors

Designer to choose colors to be used in the design.

Requirements
Must have
• Gold foil accents

```html
<!DOCTYPE html>
<html lang="en">
<head>
<meta charset="utf-8">
<title>The Loom Briefing – Business Cards</title>
<link rel="stylesheet" href="https://fonts.googleapis.com/css2?family=Dancing+Script:wght@600&family=Raleway:wght@400;600&display=swap">
<style>
  :root {
    --backdrop: #c9c9c9;
    --card-navy: #141b2e;
    --foil-gold: #d4ad4c;
    --ink-white: #f4f4f4;
    --text-light: #dfe2ea;
  }
  * { margin: 0; padding: 0; box-sizing: border-box; }
  html, body {
    width: 1200px;
    height: 852px;
    overflow: hidden;
  }
  body {
    background: var(--backdrop);
    font-family: "Raleway", Arial, sans-serif;
    display: flex;
    align-items: center;
    justify-content: center;
    gap: 40px;
  }
  .card {
    position: relative;
    width: 520px;
    height: 304px;
    background: var(--card-navy);
    border-radius: 22px;
    box-shadow: 0 6px 16px rgba(0,0,0,0.18);
  }
  .card-front {
    display: flex;
    align-items: center;
    justify-content: center;
  }
  .brand-name {
    font-family: "Raleway", Arial, sans-serif;
    font-weight: 600;
    text-transform: uppercase;
    letter-spacing: 3px;
    text-align: center;
    line-height: 1.15;
  }
  .card-front .brand-name {
    color: var(--foil-gold);
    font-size: 34px;
  }
  .card-back .brand-name {
    position: absolute;
    right: 34px;
    top: 62px;
    color: var(--ink-white);
    font-size: 24px;
  }
  .holder {
    position: absolute;
    left: 36px;
    top: 72px;
  }
  .holder-name {
    font-family: "Dancing Script", cursive;
    font-weight: 600;
    color: var(--foil-gold);
    font-size: 30px;
    line-height: 1.1;
  }
  .holder-title {
    color: var(--text-light);
    font-size: 12px;
    margin-top: 4px;
  }
  .contact-list {
    position: absolute;
    left: 36px;
    bottom: 34px;
    list-style: none;
  }
  .contact-item {
    display: flex;
    align-items: center;
    gap: 10px;
    color: var(--text-light);
    font-size: 13px;
    line-height: 22px;
  }
  .contact-icon {
    width: 13px;
    height: 13px;
    flex: none;
  }
  .contact-icon * {
    fill: none;
    stroke: var(--foil-gold);
    stroke-width: 1.4;
  }
</style>
</head>
<body>
  <section class="card card-front" aria-label="Card front">
    <div class="brand-name">The Loom<br>Briefing</div>
  </section>

  <section class="card card-back" aria-label="Card back">
    <div class="holder">
      <div class="holder-name">Belinda Harwick</div>
      <div class="holder-title">Director and Stylist</div>
    </div>

    <ul class="contact-list">
      <li class="contact-item">
        <svg class="contact-icon" viewBox="0 0 14 14" aria-hidden="true">
          <circle cx="7" cy="7" r="6"/>
          <path d="M5 4.2l1 1.6-.7.8c.4.9 1.1 1.6 2 2l.8-.7 1.6 1-.5 1c-2.5-.3-4.6-2.4-5-5z"/>
        </svg>
        +61 8 7142 5809
      </li>
      <li class="contact-item">
        <svg class="contact-icon" viewBox="0 0 14 14" aria-hidden="true">
          <rect x="1" y="3" width="12" height="8"/>
          <path d="M1 3l6 4.5L13 3"/>
        </svg>
        belinda@theloombriefing.example
      </li>
      <li class="contact-item">
        <svg class="contact-icon" viewBox="0 0 14 14" aria-hidden="true">
          <circle cx="7" cy="7" r="6"/>
          <ellipse cx="7" cy="7" rx="2.6" ry="6"/>
          <path d="M1 7h12"/>
        </svg>
        www.theloombriefing.example
      </li>
    </ul>

    <div class="brand-name">The Loom<br>Briefing</div>
  </section>
</body>
</html>
```